Business Card Design Project

Business Card
We are rebranding with a new logo
Industry/Entity Type
Business
Contact Information for Business Card
Dennis Morvale +61 487215963 dennis@quorv.com.au P.O. Box 872 Fernlow QLD 4309
Requirements
Must have
- Logo

```html
<!DOCTYPE html>
<html lang="en">
<head>
<meta charset="utf-8">
<title>Quorv International – Business Card</title>
<link rel="stylesheet" href="https://fonts.googleapis.com/css2?family=Lato:wght@400;700;900&display=swap">
<style>
  :root {
    --backdrop: #3a3b3d;
    --card: #fbfbfa;
    --ink: #1c1c1c;
    --orange: #f07d1a;
    --blue: #1f8cc4;
    --blue-deep: #12689a;
    --rule: #c9c9c9;
  }
  * { box-sizing: border-box; margin: 0; padding: 0; }
  html, body { width: 1200px; height: 926px; overflow: hidden; }
  body {
    background: var(--backdrop);
    font-family: "Lato", sans-serif;
    position: relative;
  }
  .business-card {
    position: absolute;
    left: 150px;
    top: 213px;
    width: 900px;
    height: 500px;
    background: var(--card);
    overflow: hidden;
    box-shadow: 0 18px 40px rgba(0,0,0,0.35);
  }
  .card-decoration {
    position: absolute;
    left: 0;
    right: 0;
    bottom: 0;
    height: 150px;
    background: linear-gradient(100deg, var(--orange) 0%, var(--blue) 30%, var(--blue-deep) 100%);
  }
  .brand {
    position: absolute;
    left: 64px;
    top: 78px;
    display: flex;
    align-items: center;
    gap: 14px;
  }
  .brand-dot {
    width: 26px; height: 26px; border-radius: 50%;
    background: var(--blue);
  }
  .brand-name {
    font-weight: 700;
    font-size: 30px;
    letter-spacing: 2px;
    color: var(--blue);
    text-transform: uppercase;
  }
  .holder {
    position: absolute;
    right: 64px;
    top: 138px;
    text-align: right;
  }
  .holder-name {
    font-size: 32px;
    font-weight: 400;
    color: var(--orange);
    text-transform: uppercase;
    letter-spacing: 0.5px;
    margin-bottom: 14px;
  }
  .holder-name strong { font-weight: 900; }
  .contact-list { list-style: none; }
  .contact-item {
    display: flex;
    justify-content: flex-end;
    align-items: center;
    gap: 14px;
    font-size: 22px;
    color: var(--ink);
    letter-spacing: 0.4px;
    padding: 3px 0 4px;
    border-top: 1px solid var(--rule);
  }
  .contact-item:last-child { border-bottom: 1px solid var(--rule); }
  .contact-icon { width: 18px; height: 18px; flex: none; }
  .contact-icon path, .contact-icon rect { fill: var(--orange); }
</style>
</head>
<body>
  <article class="business-card">
    <div class="card-decoration" role="img" aria-label="Orange and blue wave decoration along the bottom of the card"></div>

    <div class="brand">
      <span class="brand-dot"></span>
      <span class="brand-name">Quorv International</span>
    </div>

    <div class="holder">
      <h1 class="holder-name">Dennis <strong>Morvale</strong></h1>
      <ul class="contact-list">
        <li class="contact-item">+61 487215963
          <svg class="contact-icon" viewBox="0 0 18 18" aria-hidden="true"><path d="M2,5 C2,3 5,2 9,2 C13,2 16,3 16,5 L16,7 L12,7 L12,5 L6,5 L6,7 L2,7 Z"/><rect x="4" y="8" width="10" height="8" rx="1"/></svg>
        </li>
        <li class="contact-item">dennis@quorv.com.au
          <svg class="contact-icon" viewBox="0 0 18 18" aria-hidden="true"><path d="M1,4 L17,4 L17,14 L1,14 Z M2,5 L9,10 L16,5 L16,6 L9,11 L2,6 Z" fill-rule="evenodd"/></svg>
        </li>
        <li class="contact-item">P.O. Box 872 Fernlow QLD 4309
          <svg class="contact-icon" viewBox="0 0 18 18" aria-hidden="true"><path d="M9,1 C5.5,1 3,3.5 3,7 C3,11 9,17 9,17 C9,17 15,11 15,7 C15,3.5 12.5,1 9,1 Z M9,4.5 A2.5,2.5 0 1 0 9,9.5 A2.5,2.5 0 1 0 9,4.5 Z" fill-rule="evenodd"/></svg>
        </li>
      </ul>
    </div>
  </article>
</body>
</html>
```